Medical consulting firm needs polished website

I am a physician and working on setting up a smal consulting firm in New Hampshire, USA. It is called Bright Harbor Medical Services, LLC and the website will be BrightHarborMed.com. I was puttering around at making my own website, and it just didn't come together nicely so I've decided to leave it to the pros. The focus of the business is Advanced Care Planning, ie planning for your future medical needs. So it deals with some heavy stuff like planning for if you get sick, who should make decisions for you, end of life options etc. So it can't be too flippant or cutesy, but also can't be too dour and dark. I am hoping to convey that by thinking ahead and making some plans you can lift some of the worries off of yourself and your family - and that we can help make a scary sounding path more manageable. I want it to be made with wordpress and I have actually already bought a template ( Vitarun – A Modern Multidisciplinary Medical & Health Theme ). The website needs to have general information about our services, doc profile, appointment maker, blog/url link page, and ideally web commerce application ( the template has access to woocommerce). I've posted my business card and current brochure (still tweaking them, but you get the idea). I am also partnering with lumenfold.com and so have included their logo and would want connections/info about them. I have the logos etc in different formats as needed.

Target Market(s)

middle aged to older adults

Industry/Entity Type

Medical

Coding

Coded - Design and coding required

Font styles to use
Sans Serif

Requirements
Must have
• as above.
Nice to have
• Ease of reading/access for elderly viewers. woo commerce.

```html
<!DOCTYPE html>
<html lang="en">
<head>
<meta charset="utf-8">
<title>Bright Harbor Medical Services</title>
<link href="https://fonts.googleapis.com/css2?family=Roboto+Condensed:wght@400;700&family=Nothing+You+Could+Do&display=swap" rel="stylesheet">
<style>
  :root {
    --hero-dark: #2f3a4c;
    --hero-mid: #56657c;
    --hero-light: #a9b6c8;
    --band-blue: #4a9ee8;
    --band-light: #6cb6f2;
    --accent-blue: #1f7fd4;
    --white: #ffffff;
    --ink: #222831;
    --rule: rgba(255,255,255,0.35);
  }
  * { box-sizing: border-box; margin: 0; padding: 0; }
  html, body { width: 1200px; height: 676px; overflow: hidden; background: #ffffff; }
  body { font-family: "Roboto Condensed", Arial, sans-serif; color: var(--ink); }

  .site { position: relative; width: 1200px; height: 676px; overflow: hidden; }

  .hero { position: relative; height: 490px; }
  .hero-photo {
    position: absolute; inset: 0;
    background:
      radial-gradient(ellipse at 78% 70%, rgba(74,120,200,0.55), transparent 55%),
      radial-gradient(ellipse at 70% 30%, rgba(220,225,235,0.45), transparent 50%),
      linear-gradient(120deg, var(--hero-dark) 0%, var(--hero-mid) 45%, var(--hero-light) 75%, var(--hero-mid) 100%);
  }
  .hero-shade { position: absolute; inset: 0; background: rgba(20,28,44,0.35); }

  .site-header {
    position: absolute; top: 0; left: 0; right: 0; height: 72px;
    display: flex; align-items: center; padding: 0 40px;
    border-bottom: 1px solid var(--rule);
  }
  .brand { display: flex; align-items: center; gap: 10px; text-decoration: none; }
  .brand-dot { width: 44px; height: 44px; border-radius: 50%; background: var(--band-blue); }
  .brand-name { font-size: 28px; font-weight: 400; color: var(--white); }
  .main-nav { display: flex; gap: 36px; margin-left: 64px; }
  .main-nav a { color: var(--white); text-decoration: none; font-size: 16px; font-weight: 700; letter-spacing: 0.3px; }
  .header-actions { margin-left: auto; display: flex; gap: 10px; }
  .btn-pill { font-size: 13px; padding: 7px 12px; border-radius: 16px; text-decoration: none; font-family: Arial, sans-serif; }
  .btn-login { color: var(--white); border: 1.5px solid var(--white); }
  .btn-quote { color: var(--ink); background: var(--white); border: 1.5px solid var(--white); }

  .hero-copy { position: absolute; top: 195px; left: 0; right: 0; text-align: center; color: var(--white); }
  .hero-title { font-family: "Nothing You Could Do", cursive; font-size: 40px; font-weight: 400; line-height: 1.05; letter-spacing: 2px; }
  .hero-text { margin-top: 22px; font-size: 16px; line-height: 1.25; }
  .btn-register {
    display: inline-block; margin-top: 24px; background: var(--white); color: var(--accent-blue);
    font-size: 10px; font-weight: 700; padding: 10px 14px; border-radius: 3px; text-decoration: none;
  }

  .intro-band {
    height: 104px; background: linear-gradient(90deg, var(--band-blue), var(--band-light));
    color: var(--white); text-align: center; padding: 10px 60px 0;
  }
  .intro-title { font-size: 22px; font-weight: 700; }
  .rule-dashed { border: 0; border-top: 1.5px dashed currentColor; opacity: 0.8; margin: 8px 0 12px; }
  .intro-text { font-size: 13px; line-height: 1.4; }

  .services { text-align: center; padding-top: 14px; color: var(--accent-blue); }
  .services-title { font-size: 22px; font-weight: 700; color: var(--ink); }
  .services-title span { color: var(--accent-blue); }
  .services .rule-dashed { margin: 12px 40px 0; }
</style>
</head>
<body>
<div class="site">
  <section class="hero">
    <div class="hero-photo" role="img" aria-label="Blurred office photo of a desk with reading glasses and printed bar charts"></div>
    <div class="hero-shade"></div>

    <header class="site-header">
      <a class="brand" href="#"><span class="brand-dot"></span><span class="brand-name">Bright Harbor</span></a>
      <nav class="main-nav">
        <a href="#">HOME</a><a href="#">ABOUT</a><a href="#">SERVICES</a><a href="#">BLOG</a><a href="#">SHOP</a><a href="#">CONTACT</a>
      </nav>
      <div class="header-actions">
        <a class="btn-pill btn-login" href="#">Log In</a>
        <a class="btn-pill btn-quote" href="#">Request a Quote</a>
      </div>
    </header>

    <div class="hero-copy">
      <h1 class="hero-title">Prepare Today Because<br>Someday is Soon</h1>
      <p class="hero-text">We are available to meet with you in the privacy of your own home or in<br>our office and provide notary services.</p>
      <a class="btn-register" href="#">REGISTER NOW</a>
    </div>
  </section>

  <section class="intro-band">
    <h2 class="intro-title">Bright Harbor Medical Services, LLC</h2>
    <hr class="rule-dashed">
    <p class="intro-text">Advanced Care Planning helps your voice to always be heard. None of us like to think about getting sick, injured, or even dying but.. unfortunately wishful thinking doesn't protect us, but<br>making a plan can help. We are here to help you achieve the peace of mind that comes from taking charge!</p>
  </section>

  <section class="services">
    <h2 class="services-title">Our <span>Services</span></h2>
    <hr class="rule-dashed">
  </section>
</div>
</body>
</html>
```